Web Site Design and Business Card design for Recruiting Company

There are three major tasks in this project:
1) I need to re-design my newly created website www.talvoro.net using the same logo but creating a totally different recruiting template that will apply better for a recruitment site. I want to use the elements of the Talvoro Network logo (which is the road junction) and red, black and gray colors throughout the website. I need someone to both design and launch the site...
2) I would also like to design a double sided business card using the same logo/colors and elements as described above
3) I would also like to have a small thumbnail logo created. As our large logo cannot be previewed easily on the Pelmwork or on Google Chrome tab images

The design should be contemporary, minimalist and slick

```html
<!DOCTYPE html>
<html lang="en">
<head>
<meta charset="utf-8">
<title>Talvoro Network</title>
<link href="https://fonts.googleapis.com/css2?family=Poppins:wght@600;700;800&family=Open+Sans:wght@400;600&family=Roboto:wght@400;500&display=swap" rel="stylesheet">
<style>
:root{
  --red:#e31b2d;
  --red-dark:#c8101f;
  --ink:#1b1b1b;
  --text:#333;
  --muted:#666;
  --gray-bg:#f3f3f3;
  --card-head:#f5eeee;
  --footer:#2b2b2b;
  --footer-line:#444;
  --white:#fff;
}
*{box-sizing:border-box;margin:0;padding:0}
html,body{width:1200px;height:2893px;overflow:hidden}
body{font-family:"Open Sans",sans-serif;color:var(--text);background:var(--white);position:relative}
.abs{position:absolute}

/* hero */
.hero{position:absolute;left:0;top:0;width:1200px;height:777px;background:linear-gradient(180deg,#8a8a8a 0%,#9b9b9b 40%,#6d6d6d 70%,#3e3e3e 100%)}
.hero-photo{position:absolute;left:0;top:430px;width:1200px;height:347px;background:linear-gradient(180deg,rgba(60,60,60,0) 0%,rgba(40,40,45,.55) 35%,rgba(30,30,35,.75) 100%)}
.brand{position:absolute;left:112px;top:31px;width:154px;height:100px;display:flex;align-items:center;gap:8px}
.brand-dot{width:12px;height:12px;background:var(--red);border-radius:50%}
.brand-name{font-family:"Open Sans",sans-serif;font-weight:600;font-size:17px;color:var(--white);line-height:1.2}
.nav{position:absolute;top:70px;left:360px;display:flex;gap:44px}
.nav a{font-family:"Open Sans",sans-serif;font-weight:600;font-size:15.5px;color:var(--white);text-decoration:none;position:relative}
.nav a.active{color:var(--red)}
.nav a.active::after{content:"";position:absolute;left:0;right:0;top:26px;height:3px;background:var(--red)}
.search-icon{position:absolute;left:1074px;top:73px}
.hero h1{position:absolute;top:218px;width:1200px;text-align:center;font-family:"Poppins",sans-serif;font-weight:800;font-size:84px;color:var(--white);letter-spacing:-1px}
.hero .tagline{position:absolute;top:306px;width:1200px;text-align:center;font-size:19px;color:var(--white)}
.search{position:absolute;top:369px;left:125px;display:flex;gap:10px}
.field{width:230px;height:49px;background:var(--white);display:flex;align-items:center;justify-content:space-between;padding:0 21px;font-size:13.5px;color:#222}
.field.placeholder{color:#999}
.caret{width:0;height:0;border-left:5px solid transparent;border-right:5px solid transparent;border-top:6px solid #222}
.btn-search{width:229px;height:49px;background:var(--red);color:var(--white);display:flex;align-items:center;justify-content:center;gap:8px;font-size:13.5px}
.dots{position:absolute;top:725px;left:577px;display:flex;gap:14px}
.dots span{width:12px;height:12px;border-radius:50%;background:var(--white)}
.dots span.on{background:transparent;border:2px solid var(--white)}

/* about */
.about{position:absolute;top:777px;left:0;width:1200px;height:422px;background:linear-gradient(120deg,#e31b2d 0%,#e01d2f 50%,#c80f1e 100%);color:var(--white);text-align:center}
.about-figure{position:absolute;left:360px;top:160px;width:480px;height:262px;background:linear-gradient(180deg,rgba(150,0,10,0) 0%,rgba(150,0,10,.35) 100%)}
.about h2{position:absolute;top:66px;width:1200px;font-family:"Poppins",sans-serif;font-weight:700;font-size:35px}
.about p{position:absolute;top:136px;left:175px;width:850px;font-size:16.5px;line-height:26.5px}
.stats{position:absolute;top:255px;left:0;width:1200px}
.stat{position:absolute;width:200px;text-align:center}
.stat b{display:block;font-family:"Poppins",sans-serif;font-weight:700;font-size:44px;line-height:60px}
.stat span{display:block;font-size:17px;margin-top:6px}

/* categories */
.cats{position:absolute;top:1199px;left:0;width:1200px;height:774px;background:var(--gray-bg)}
.cats h2{position:absolute;top:78px;width:1200px;text-align:center;font-family:"Poppins",sans-serif;font-weight:700;font-size:31.5px;line-height:36px;color:var(--ink)}
.card{position:absolute;top:203px;left:111px;width:977px;height:498px;background:var(--white);box-shadow:0 1px 4px rgba(0,0,0,.15)}
.card-head{height:68px;background:var(--card-head);position:relative}
.card-head h3{position:absolute;top:24px;font-family:"Open Sans",sans-serif;font-weight:600;font-size:15.5px;color:var(--red)}
.col{position:absolute;top:92px}
.col li{list-style:none;height:28.3px;font-family:"Roboto",sans-serif;font-size:12.6px;color:#222;position:relative}
.col li::after{content:"";position:absolute;top:5px;width:5px;height:5px;border-right:1.3px solid #333;border-top:1.3px solid #333;transform:rotate(45deg)}
.col.c1{left:35px}.col.c1 li::after{left:265px}
.col.c2{left:386px}.col.c2 li::after{left:223px}
.col.c3{left:712px}.col.c3 li::after{left:222px}

/* posts */
.posts-title{position:absolute;top:2034px;width:1200px;text-align:center;font-family:"Roboto",sans-serif;font-weight:500;font-size:30px;color:var(--ink)}
.posts-sub{position:absolute;top:2087px;width:1200px;text-align:center;font-size:16px;color:#333}
.post{position:absolute;top:2150px;width:308px}
.post-img{height:156px}
.post h4{margin:20px 0 0 5px;font-family:"Roboto",sans-serif;font-weight:400;font-size:18.5px;color:#222}
.post time{display:block;margin:6px 0 0 7px;font-size:10px;color:#444}
.post p{margin:10px 0 0 5px;font-size:12.6px;line-height:20px;color:#222;width:290px}
.read{display:inline-flex;align-items:center;gap:6px;margin:22px 0 0 6px;width:123px;height:42px;justify-content:center;background:var(--red);color:var(--white);font-family:"Roboto",sans-serif;font-weight:500;font-size:11.5px}

/* footer */
.footer{position:absolute;top:2584px;left:0;width:1200px;height:309px;background:var(--footer);color:#cfcfcf}
.footer h5{position:absolute;top:46px;font-family:"Poppins",sans-serif;font-weight:600;font-size:15.5px;color:var(--white)}
.flinks{position:absolute;top:95px;font-size:13px;line-height:30px;list-style:none}
.contact{position:absolute;left:548px;top:95px;font-size:13px}
.contact div{display:flex;gap:8px;margin-bottom:20px;line-height:16px}
.social{position:absolute;left:939px;top:111px;display:flex;gap:8px}
.social span{width:31px;height:31px;border-radius:50%;background:var(--red)}
.footer hr{position:absolute;top:250px;left:111px;width:977px;border:0;border-top:1px solid var(--footer-line)}
.copy{position:absolute;top:270px;left:111px;font-size:11.5px}
.legal{position:absolute;top:270px;left:908px;font-size:9.5px;color:#777}
</style>
</head>
<body>

<header class="hero">
  <div class="hero-photo" role="img" aria-label="Photo of six smiling business professionals seated in a row against a grey brick wall"></div>
  <div class="brand"><span class="brand-dot"></span><span class="brand-name">Talvoro Network</span></div>
  <nav class="nav">
    <a class="active">HOME</a><a>ABOUT US</a><a>SERVICES</a><a>PARTNERS</a><a>BLOG</a><a>CONTACT US</a>
  </nav>
  <svg class="search-icon" width="15" height="15" viewBox="0 0 15 15"><circle cx="6" cy="6" r="4.5" fill="none" stroke="#fff" stroke-width="2"/><line x1="9.5" y1="9.5" x2="13.5" y2="13.5" stroke="#fff" stroke-width="2.2"/></svg>
  <h1>Talvoro Network</h1>
  <div class="tagline">Find your dream jobs in our powerful career Talvoro Network</div>
  <div class="search">
    <div class="field placeholder">Job title, keywords...</div>
    <div class="field">Anywhere <span class="caret"></span></div>
    <div class="field">Full Time <span class="caret"></span></div>
    <div class="btn-search"><svg width="12" height="12" viewBox="0 0 12 12"><circle cx="5" cy="5" r="3.6" fill="none" stroke="#fff" stroke-width="1.6"/><line x1="7.8" y1="7.8" x2="11" y2="11" stroke="#fff" stroke-width="1.8"/></svg>Search Job</div>
  </div>
  <div class="dots"><span class="on"></span><span></span><span></span></div>
</header>

<section class="about">
  <div class="about-figure" role="img" aria-label="Faint image of a person walking up red stairs"></div>
  <h2>About Talvoro Network</h2>
  <p>Talvoro Network LLC is an Atlanta based talent advisory, recruiting and staffing firm. We help companies find skilled professionals within the shortest time frames though our unique network of business and personal connections nationwide and overseas.</p>
  <div class="stats">
    <div class="stat" style="left:174px"><b>1,930</b><span>Candidates</span></div>
    <div class="stat" style="left:388px"><b>54</b><span>Jobs Posted</span></div>
    <div class="stat" style="left:603px"><b>120</b><span>Jobs Filled</span></div>
    <div class="stat" style="left:826px"><b>550</b><span>Companies</span></div>
  </div>
</section>

<section class="cats">
  <h2>We specialize in sourcing, recruiting, placement and staffing<br>of candidates in the following categories:</h2>
  <div class="card">
    <div class="card-head">
      <h3 style="left:34px">Information Technology (IT)</h3>
      <h3 style="left:386px">Telecommunications</h3>
      <h3 style="left:712px">Accounting &amp; Finance</h3>
    </div>
    <ul class="col c1">
      <li>Project Management</li><li>Web and Application Development</li><li>Network Administration</li><li>System Engineering and Administration</li><li>Software Engineering</li><li>Mobile Development</li><li>Data Base Development and Management</li><li>Technical Support</li><li>Quality Assurance</li><li>ERP and CRM Consulting</li><li>Bussiness Intelligence (BI)</li><li>Big Data Analytics</li><li>Reporting and Data Visualization</li>
    </ul>
    <ul class="col c2">
      <li>Project Management</li><li>Construction Management</li><li>Site Acquisition</li><li>L&amp;A Installation and Civil Work</li><li>RF Engineering and Network Design</li><li>Cell Site Integration</li><li>Network Optimization</li><li>Site Maintenance</li><li>Quality Assurance</li><li>Site Scoping and Project Controls</li><li>Project Support</li>
    </ul>
    <ul class="col c3">
      <li>Financial Planning</li><li>Financial Management</li><li>Certified Public Accounting (CPA)</li><li>Audit</li><li>Cost Accounting</li><li>Accounts Receivable</li><li>Accounts Payable</li><li>Business Analysis</li><li>Credits and Collections</li><li>Payroll</li>
    </ul>
  </div>
</section>

<h2 class="posts-title">RECENT POSTS</h2>
<p class="posts-sub">At vero eos et accusamus et iusto odio dignissimos ducimus</p>

<article class="post" style="left:111px">
  <div class="post-img" role="img" aria-label="Photo of business people looking at a laptop in a city setting" style="background:linear-gradient(135deg,#6b6f78,#2b2e35)"></div>
  <h4>JOB SEARCH</h4><time>AUGUST 15, 2019</time>
  <p>Class aptent taciti sociosqu ad litora torquent per co nubia nostra per inceptos hymenaeos</p>
  <span class="read">READ MORE <svg width="9" height="9" viewBox="0 0 9 9"><circle cx="4.5" cy="4.5" r="4.5" fill="#fff"/><path d="M3.6 2.5 5.6 4.5 3.6 6.5" stroke="#e31b2d" stroke-width="1.3" fill="none"/></svg></span>
</article>
<article class="post" style="left:445px">
  <div class="post-img" role="img" aria-label="Photo of colleagues discussing plans at a meeting table" style="background:linear-gradient(135deg,#b9c3cc,#5c6a78)"></div>
  <h4>EMPLOYERS</h4><time>JULY 2, 2019</time>
  <p>Class aptent taciti sociosqu ad litora torquent per co nubia nostra per inceptos hymenaeos</p>
  <span class="read">READ MORE <svg width="9" height="9" viewBox="0 0 9 9"><circle cx="4.5" cy="4.5" r="4.5" fill="#fff"/><path d="M3.6 2.5 5.6 4.5 3.6 6.5" stroke="#e31b2d" stroke-width="1.3" fill="none"/></svg></span>
</article>
<article class="post" style="left:780px">
  <div class="post-img" role="img" aria-label="Photo of candidates waiting in a bright modern office lobby" style="background:linear-gradient(135deg,#d6d6d2,#7e7c76)"></div>
  <h4>CANDIDATES</h4><time>JUNE 30, 2019</time>
  <p>Class aptent taciti sociosqu ad litora torquent per co nubia nostra per inceptos hymenaeos</p>
  <span class="read">READ MORE <svg width="9" height="9" viewBox="0 0 9 9"><circle cx="4.5" cy="4.5" r="4.5" fill="#fff"/><path d="M3.6 2.5 5.6 4.5 3.6 6.5" stroke="#e31b2d" stroke-width="1.3" fill="none"/></svg></span>
</article>

<footer class="footer">
  <h5 style="left:111px">Company</h5>
  <h5 style="left:548px">Contact Us</h5>
  <h5 style="left:938px">Connect With Us</h5>
  <ul class="flinks" style="left:112px"><li>Home</li><li>About Us</li><li>Services</li><li>Partners</li></ul>
  <ul class="flinks" style="left:318px"><li>Recent Blog</li><li>Gallery</li><li>Contact Us</li></ul>
  <div class="contact">
    <div><svg width="10" height="14" viewBox="0 0 10 14"><path d="M5 0a5 5 0 0 1 5 5c0 4-5 9-5 9S0 9 0 5a5 5 0 0 1 5-5z" fill="#fff"/><circle cx="5" cy="5" r="1.8" fill="#2b2b2b"/></svg><span>Talvoro Network LLC, Street Name,<br>City Address, Atlanta.</span></div>
    <div><svg width="13" height="13" viewBox="0 0 13 13"><path d="M3 0 5 3 3.6 4.6c.9 2 2.6 3.7 4.6 4.6L9.8 7.8 13 9.8 12 12.5C6 12.5.5 7 .5 1z" fill="#fff"/></svg><span>+1-555-014-2278</span></div>
    <div><svg width="13" height="10" viewBox="0 0 13 10"><rect width="13" height="10" rx="1" fill="#fff"/><path d="M0 1 6.5 6 13 1" stroke="#2b2b2b" stroke-width="1.2" fill="none"/></svg><span>info@talvoro.net</span></div>
  </div>
  <div class="social" aria-label="Social media links"><span></span><span></span><span></span><span></span></div>
  <hr>
  <div class="copy">Copyrights © 2019 Talvoro Network LLC. All rights reserved.</div>
  <div class="legal">Terms and Conditions | Privacy Policy</div>
</footer>

</body>
</html>
```